Veldmark Supplies Business Card

Professional business card that stand out to our potential customers. Front and back with clean modern design

Industry/Entity Type

Oil and gas

Contact Information for Business Card

Name, address, website , office phone and cell number

Requirements
Must have
• Editable files for each employee

```html
<!DOCTYPE html>
<html lang="en">
<head>
<meta charset="UTF-8">
<title>Veldmark Supplies Business Card</title>
<link href="https://fonts.googleapis.com/css2?family=Montserrat:wght@400;500;700;800&display=swap" rel="stylesheet">
<style>
  :root {
    --brand-red: #e82027;
    --brand-blue: #0aafd3;
    --paper: #ffffff;
    --backdrop: #8c8c8c;
    --backdrop-light: #e6e6e6;
  }
  * { box-sizing: border-box; margin: 0; padding: 0; }
  html, body { width: 1200px; height: 856px; overflow: hidden; }
  body {
    background: linear-gradient(180deg, var(--backdrop-light) 0%, var(--backdrop) 100%);
    font-family: "Montserrat", sans-serif;
    position: relative;
  }
  .card {
    position: absolute;
    left: 280px;
    width: 640px;
    height: 366px;
    overflow: hidden;
    box-shadow: 0 14px 30px rgba(0,0,0,0.35);
  }
  .card-front { top: 40px; background: var(--paper); }
  .card-back { top: 450px; background: var(--brand-red); }

  .front-wave { position: absolute; inset: 0; width: 100%; height: 100%; }

  .front-brand {
    position: absolute;
    left: 40px;
    top: 145px;
    display: flex;
    align-items: center;
    gap: 10px;
  }
  .brand-square {
    width: 22px; height: 22px;
    background: var(--brand-blue);
    flex: none;
  }
  .brand-name {
    font-weight: 800;
    font-size: 20px;
    line-height: 1.15;
    letter-spacing: 1px;
    text-transform: uppercase;
    color: var(--brand-red);
  }
  .front-brand .brand-name span { display: block; }

  .contact {
    position: absolute;
    right: 70px;
    top: 42px;
    text-align: right;
    color: var(--paper);
    font-size: 14px;
    line-height: 1.45;
  }
  .contact-name { font-weight: 700; font-size: 17px; letter-spacing: 0.5px; text-transform: uppercase; }
  .contact-title { font-size: 14px; margin-bottom: 10px; }
  .contact-address { margin-bottom: 10px; }
  .contact-lines { margin-bottom: 10px; }

  .icon-column {
    position: absolute;
    right: 22px;
    top: 150px;
    display: flex;
    flex-direction: column;
    gap: 10px;
  }
  .icon {
    width: 22px; height: 22px;
    background: var(--brand-blue);
    display: flex; align-items: center; justify-content: center;
  }
  .icon svg { width: 14px; height: 14px; }

  .back-brand {
    position: absolute;
    inset: 0;
    display: flex;
    align-items: center;
    justify-content: center;
    gap: 16px;
  }
  .back-brand .brand-square { width: 34px; height: 34px; }
  .back-brand .brand-name { color: var(--paper); font-size: 38px; letter-spacing: 2px; }
</style>
</head>
<body>

<section class="card card-front">
  <svg class="front-wave" viewBox="0 0 640 366" preserveAspectRatio="none">
    <path d="M400 0 C 300 110, 340 280, 0 330 L 0 366 L 640 366 L 640 0 Z" fill="var(--brand-red)"/>
    <path d="M382 0 C 284 110, 322 270, 0 318" fill="none" stroke="var(--brand-blue)" stroke-width="8"/>
    <path d="M368 0 C 270 110, 306 262, 0 306" fill="none" stroke="var(--brand-red)" stroke-width="3"/>
  </svg>

  <div class="front-brand">
    <span class="brand-square"></span>
    <span class="brand-name"><span>Veldmark</span><span>Supplies</span></span>
  </div>

  <div class="contact">
    <div class="contact-name">Dara Holloway</div>
    <div class="contact-title">President</div>
    <div class="contact-address">418 Calloway St, Ste<br>200, Dallas, TX 75204</div>
    <div class="contact-lines">555-214-3380<br>555-014-9926</div>
    <div>info@veldmark-mail.com<br>www.veldmark-supplies.com</div>
  </div>

  <div class="icon-column">
    <span class="icon"><svg viewBox="0 0 14 14"><path d="M3 1 L5 1 L6 4 L4.5 5 Q6 8 9 9.5 L10 8 L13 9 L13 11 Q12 13 10 13 Q2 11 1 3 Q1 1 3 1 Z" fill="#fff"/></svg></span>
    <span class="icon"><svg viewBox="0 0 14 14"><rect x="3.5" y="1" width="7" height="12" rx="1" fill="none" stroke="#fff" stroke-width="1.4"/><circle cx="7" cy="11" r="0.8" fill="#fff"/></svg></span>
    <span class="icon"><svg viewBox="0 0 14 14"><rect x="1" y="3" width="12" height="8" fill="none" stroke="#fff" stroke-width="1.4"/><path d="M1 3 L7 8 L13 3" fill="none" stroke="#fff" stroke-width="1.4"/></svg></span>
    <span class="icon"><svg viewBox="0 0 14 14"><circle cx="7" cy="7" r="5.5" fill="none" stroke="#fff" stroke-width="1.3"/><ellipse cx="7" cy="7" rx="2.3" ry="5.5" fill="none" stroke="#fff" stroke-width="1"/><path d="M1.5 7 H12.5" stroke="#fff" stroke-width="1"/></svg></span>
  </div>
</section>

<section class="card card-back">
  <div class="back-brand">
    <span class="brand-square"></span>
    <span class="brand-name">Veldmark Supplies</span>
  </div>
</section>

</body>
</html>
```